Commercial Rooftop Solar business needs a website

We need a website with fantastic appeal for a new company based in Melbourne called Tallow Ridge Energy. We design and install solar energy systems for commercial applications across Australia. Our market is to focus on small to medium businesses looking for solar solutions, but we will also provide our service for residential customers. We would like a beautiful 'front page' feel to our home page, using photographs of solar PV systems and/or natural imagery. Our logo uses the colours orange and black, which could easily be echoed in photographic imagery of sunset and sunrise, for example. The design should communicate quiet confidence and professionalism to a corporate marketplace.

NEW POINTS FOR BRIEF: This design also needs to be flexible to allow for additional future content, including a Support page with sub pages, FAQ's, and a Blog.

As part of this design project, we will require the coding for the website to be completed by the designer.

We have seen some websites, which we like the look and feel of: these are listed below.

brightvanepower.com.au:

• Beautiful images underlaying brief text selling points.
• Simple ‘front cover’ style home page with elegant drop-down menu, stylish simple font style.
• Home page invites exploration through the menu links, rather than trying to provide all the information up front.
• Company logo and name in the top left hand corner, contact details accessible at top right hand, seems consistent in most sites.

kelpworks.com.au

rumbofield.com:
• Same element as the others is the front-page style home page with beautiful images underlying text.

We have a webpage that we started uploading content to. You can use some of the content there in your designs: www.tallowridgeenergy.com.au

Technical Specifications:
PAGES:

Home

About Us

Solutions - Commercial
- Residential

Products - Solar Panels - Vorla Heron, Vorla TELD, Vorla QB
- Solar Inverters - Kestamo, BrilQuill
- Monitoring systems - Dunmere Metrics
- Batteries - RW

- Datasheets have been provided for reference but if it's too much work, you can use generic text and we will provide content later.

Contact Us

FUTURE PAGES (Please consider in structure, where links could be placed):

Support

FAQ's

Blog.

We could provide some content for the Support page soon, but the Blog and FAQ's are future pages which we don't want highlighted in the design as we don't yet have content.

Phone: 1800 7 BIRCH
Email: sales@tallowridgeenergy.com.au

Currently, I do not have images and text available. Please
use placeholders in the meantime. The final text and images will be uploaded for the winner once a winning design has been selected.

Target Market(s)

Primary focus is on small to medium sized business owners. Those owners will have a house which may be suitable for solar so we want to cater to residential deeper in the website.

Industry/Entity Type

Solar Energy

Coding

Coded - Design and coding required

Number of Pages Required

5+ page

Colors
f78f20
0255a3

Requirements
Must have
• Logo as per attachments.
Nice to have
• Logo can have alternate colours Eg. White on Orange or Black etc. provided colour correct logo is shown somewhere eg. footer or contact page.
• In the active site, I'd like to have:
• Very slowly zooming images - barely perceptible.
• Title text that rolls into place
• Subtle movements
• See https://plumtally.com.au/ for example

```html
<!DOCTYPE html>
<html lang="en">
<head>
<meta charset="utf-8">
<title>Contact Us – Tallow Ridge Energy</title>
<link rel="stylesheet" href="https://fonts.googleapis.com/css2?family=Lato:wght@400;700&family=Syncopate:wght@400;700&display=swap">
<style>
:root{
  --accent:#f2401c;
  --ink:#1d1d1d;
  --text:#444;
  --line:#cfcfcf;
  --footer:#1f1f1f;
  --footer-deep:#121212;
  --footer-text:#e4e4e4;
  --white:#fff;
}
*{margin:0;padding:0;box-sizing:border-box}
html,body{width:866px;height:1200px;overflow:hidden}
body{position:relative;background:var(--white);font-family:Lato,sans-serif;color:var(--text)}
.abs{position:absolute}
.display{font-family:Syncopate,sans-serif;letter-spacing:.1em}

.hero{left:0;top:0;width:866px;height:328px;background:linear-gradient(120deg,#6c6c6c 0%,#8e8e8e 45%,#9a9a9a 70%,#7a7a7a 100%)}
.brand{left:117px;top:34px;color:var(--white);font-family:Lato,sans-serif;font-weight:700;font-size:15px;letter-spacing:.06em;display:flex;align-items:center;gap:8px}
.brand-dot{width:14px;height:14px;border-radius:50%;background:var(--white)}
.top-phone{left:533px;top:15px;display:flex;align-items:center;gap:6px;color:var(--white);font-size:13px;font-weight:700}
.estimate{left:648px;top:15px;width:109px;height:22px;border-radius:11px;background:var(--accent);color:var(--white);font-size:9px;font-weight:700;display:flex;align-items:center;justify-content:center;border:1px solid rgba(255,255,255,.6)}
.nav{top:60px;font-size:9px;color:var(--white);font-weight:700}
.nav.active{color:var(--accent)}

.page-title{left:0;top:363px;width:866px;display:flex;justify-content:center;align-items:center;gap:8px;color:var(--ink);font-size:19px;font-weight:700}
.page-title::before,.page-title::after{content:"";width:55px;height:1px;background:var(--ink)}
.intro{left:0;top:424px;width:866px;text-align:center;font-size:10px;color:#333}

.form-title{left:128px;top:466px;font-size:14px;font-weight:700;color:var(--ink)}
.label{font-size:8px;color:#444}
.field{border:1px solid var(--line);background:var(--white)}
.chev{position:absolute;right:8px;top:10px}
.consent{left:125px;top:901px;width:280px;font-size:7.5px;line-height:13px;color:#444;padding-left:14px}
.consent svg{position:absolute;left:0;top:2px}
.submit{left:125px;top:943px;width:66px;height:20px;border-radius:10px;background:var(--accent);color:var(--white);font-size:7px;font-weight:700;display:flex;align-items:center;justify-content:center}
.divider{left:444px;top:510px;width:1px;height:450px;background:#e6e6e6}

.info{left:488px;display:flex;gap:8px}
.info-icon{width:23px;height:23px;border:1px solid #999;border-radius:50%;display:flex;align-items:center;justify-content:center;flex:none}
.info-title{font-size:8.5px;font-weight:700;color:var(--accent)}
.info-text{font-size:8px;color:#333;margin-top:2px}

.footer{left:0;top:1004px;width:866px;height:166px;background:var(--footer)}
.footer-bar{left:0;top:1170px;width:866px;height:30px;background:var(--footer-deep);color:#ccc;font-size:7.5px;display:flex;align-items:center;justify-content:center}
.f-head{top:1027px;font-size:9px;font-weight:700;color:var(--white);padding-bottom:6px;border-bottom:1px dotted #666}
.f-link{left:116px;font-size:8px;color:var(--footer-text)}
.f-link::before{content:"›";color:#888;margin-right:5px}
.f-input{left:260px;width:138px;background:var(--white);border-radius:2px;font-size:6.5px;color:#777;padding:2px 4px}
.f-submit{left:260px;top:1121px;width:49px;height:15px;border-radius:8px;background:var(--accent);color:var(--white);font-size:6px;font-weight:700;display:flex;align-items:center;justify-content:center}
.f-vsep{top:1040px;width:1px;height:110px;background:#333}
.f-row{left:434px;width:146px;font-size:8px;color:var(--footer-text);display:flex;align-items:center;gap:6px;padding-bottom:6px;border-bottom:1px solid #333;white-space:nowrap}
.f-brand{left:618px;top:1085px;width:156px;text-align:center;color:#cfcfcf;font-weight:700;font-size:12px;letter-spacing:.06em}
.abn{left:647px;top:1143px;width:94px;height:18px;border-radius:9px;background:#0e0e0e;color:var(--white);font-size:7.5px;display:flex;align-items:center;justify-content:center}
</style>
</head>
<body>

<div class="abs hero" role="img" aria-label="Desk photograph with keyboard, notepad, plant and coffee cup in muted tones"></div>
<div class="abs brand"><span class="brand-dot"></span>TALLOW RIDGE ENERGY</div>
<div class="abs top-phone">
  <svg width="20" height="20" viewBox="0 0 20 20"><circle cx="10" cy="10" r="9" fill="none" stroke="#fff" stroke-width="1.3"/><path d="M7 5.5l2 2-1 1.2c.6 1.3 1.6 2.3 2.9 2.9l1.2-1 2 2-1.3 1.5c-3.6-.3-6.5-3.2-6.8-6.8z" fill="#fff"/></svg>
  1800 7 BIRCH
</div>
<div class="abs estimate">FREE ESTIMATE</div>
<div class="abs nav display" style="left:411px">HOME</div>
<div class="abs nav display" style="left:481px">ABOUT US</div>
<div class="abs nav display" style="left:578px">SOLUTIONS</div>
<div class="abs nav display active" style="left:683px">CONTACT US</div>

<h1 class="abs page-title display">Contact Us</h1>
<p class="abs intro">We're here to help. Use the form or contact us on the details below and we'll be happy to answer any questions you may have.</p>

<h2 class="abs form-title display">Request Your Free Quote</h2>
<div class="abs label" style="left:125px;top:498px">First Name</div>
<div class="abs label" style="left:266px;top:498px">Last Name</div>
<div class="abs field" style="left:125px;top:512px;width:133px;height:28px"></div>
<div class="abs field" style="left:266px;top:512px;width:133px;height:28px"></div>
<div class="abs label" style="left:125px;top:549px">Email Address</div>
<div class="abs field" style="left:125px;top:563px;width:274px;height:28px"></div>
<div class="abs label" style="left:125px;top:600px">Phone Number</div>
<div class="abs field" style="left:125px;top:614px;width:274px;height:28px"></div>
<div class="abs label" style="left:125px;top:651px">Street Address</div>
<div class="abs label" style="left:326px;top:651px">Postcode</div>
<div class="abs field" style="left:125px;top:665px;width:193px;height:28px"></div>
<div class="abs field" style="left:326px;top:665px;width:73px;height:28px"></div>
<div class="abs label" style="left:125px;top:706px">Town / Suburb State</div>
<div class="abs field" style="left:125px;top:721px;width:274px;height:28px"><svg class="chev" width="8" height="6" viewBox="0 0 8 6"><path d="M1 1l3 3 3-3" fill="none" stroke="#555"/></svg></div>
<div class="abs label" style="left:125px;top:760px">I am interested in</div>
<div class="abs field" style="left:125px;top:775px;width:274px;height:28px"><svg class="chev" width="8" height="6" viewBox="0 0 8 6"><path d="M1 1l3 3 3-3" fill="none" stroke="#555"/></svg></div>
<div class="abs label" style="left:125px;top:818px">Your message</div>
<div class="abs field" style="left:125px;top:833px;width:274px;height:60px"></div>
<div class="abs consent">
  <svg width="8" height="8" viewBox="0 0 8 8"><rect x=".5" y=".5" width="7" height="7" fill="none" stroke="#555"/><path d="M1.8 4l1.5 1.5 3-3.5" fill="none" stroke="#555"/></svg>
  Yes, send me information on Tallow Ridge Energy products, offers &amp; promotions between Your message &amp; the Submit button.
</div>
<div class="abs submit display">SUBMIT</div>

<div class="abs divider"></div>

<div class="abs info" style="top:500px">
  <div class="info-icon"><svg width="10" height="12" viewBox="0 0 10 12"><path d="M5 11.5S1 7 1 4.5a4 4 0 018 0C9 7 5 11.5 5 11.5z" fill="none" stroke="#f2401c" stroke-width="1.3"/><circle cx="5" cy="4.5" r="1.3" fill="#f2401c"/></svg></div>
  <div><div class="info-title">TALLOW RIDGE ENERGY</div><div class="info-text">Melbourne, Victoria</div></div>
</div>
<div class="abs info" style="top:556px">
  <div class="info-icon"><svg width="11" height="11" viewBox="0 0 11 11"><path d="M1.5 1.5l2.3 2.3-1 1.2c.7 1.4 1.7 2.4 3.2 3.2l1.2-1 2.3 2.3-1.5 1C4.6 10.2 1 6.6.7 3z" fill="#f2401c"/></svg></div>
  <div><div class="info-title">PHONE</div><div class="info-text" style="font-weight:700">1800 7 BIRCH</div></div>
</div>
<div class="abs info" style="top:612px">
  <div class="info-icon"><svg width="11" height="8" viewBox="0 0 11 8"><rect width="11" height="8" rx="1" fill="#f2401c"/><path d="M.5 .8l5 3.5 5-3.5" fill="none" stroke="#fff" stroke-width=".9"/></svg></div>
  <div><div class="info-title">EMAIL</div><div class="info-text">enquiries@tallowridgeenergy.com.au</div></div>
</div>
<div class="abs info" style="top:668px">
  <div class="info-icon"><svg width="13" height="13" viewBox="0 0 13 13"><circle cx="6.5" cy="6.5" r="5.5" fill="none" stroke="#f2401c" stroke-width="1.2"/><path d="M1 6.5h11M6.5 1c2 2 2 9 0 11M6.5 1c-2 2-2 9 0 11" fill="none" stroke="#f2401c" stroke-width=".9"/></svg></div>
  <div><div class="info-title">WEBSITE</div><div class="info-text">www.tallowridgeenergy.com.au</div></div>
</div>

<footer class="abs footer"></footer>
<div class="abs f-head display" style="left:116px;width:100px">QUICK LINKS</div>
<div class="abs f-link" style="top:1055px">Home</div>
<div class="abs f-link" style="top:1078px">About Us</div>
<div class="abs f-link" style="top:1101px">Solutions</div>
<div class="abs f-link" style="top:1124px">Contact Us</div>
<div class="abs f-vsep" style="left:227px"></div>

<div class="abs f-head display" style="left:260px;width:138px">QUICK INQUIRY</div>
<div class="abs f-input" style="top:1054px;height:14px">Name</div>
<div class="abs f-input" style="top:1072px;height:14px">Email</div>
<div class="abs f-input" style="top:1091px;height:25px">Message</div>
<div class="abs f-submit display">SUBMIT</div>
<div class="abs f-vsep" style="left:414px"></div>

<div class="abs f-head display" style="left:436px;width:145px">CONTACT DETAILS</div>
<div class="abs f-row" style="top:1053px;align-items:flex-start">
  <svg width="8" height="10" viewBox="0 0 10 12" style="margin-top:2px"><path d="M5 11.5S1 7 1 4.5a4 4 0 018 0C9 7 5 11.5 5 11.5z" fill="#f2401c"/><circle cx="5" cy="4.5" r="1.4" fill="#1f1f1f"/></svg>
  <div><div style="font-weight:700;font-size:9.5px;color:#fff">TALLOW RIDGE ENERGY</div><div style="margin-top:3px;font-size:7.5px">Melbourne, Victoria</div></div>
</div>
<div class="abs f-row" style="top:1088px"><svg width="9" height="9" viewBox="0 0 11 11"><path d="M1.5 1.5l2.3 2.3-1 1.2c.7 1.4 1.7 2.4 3.2 3.2l1.2-1 2.3 2.3-1.5 1C4.6 10.2 1 6.6.7 3z" fill="#f2401c"/></svg>1800 7 BIRCH</div>
<div class="abs f-row" style="top:1111px"><svg width="9" height="7" viewBox="0 0 11 8"><rect width="11" height="8" rx="1" fill="#f2401c"/><path d="M.5 .8l5 3.5 5-3.5" fill="none" stroke="#1f1f1f" stroke-width=".9"/></svg>enquiries@tallowridgeenergy.com.au</div>
<div class="abs f-row" style="top:1134px;border:0;font-size:7.5px"><svg width="9" height="9" viewBox="0 0 13 13"><circle cx="6.5" cy="6.5" r="5.5" fill="none" stroke="#f2401c" stroke-width="1.3"/><path d="M1 6.5h11M6.5 1c2 2 2 9 0 11M6.5 1c-2 2-2 9 0 11" fill="none" stroke="#f2401c"/></svg>www.tallowridgeenergy.com.au</div>
<div class="abs f-vsep" style="left:613px"></div>

<div class="abs f-brand">TALLOW RIDGE ENERGY</div>
<div class="abs abn">ABN: 41 502 736 918</div>

<div class="abs footer-bar">Copyright © 2017 Tallow Ridge Energy. All Right Reserved.</div>

</body>
</html>
```